Global (re)insurance broker needs a business card design

We need a classic business card for our company that is headquartered in SG, with offices in Malaysia and Dubai. We specialise in insurance and reinsurance broking and consultancy for our global clients.

```html
<!DOCTYPE html>
<html lang="en">
<head>
<meta charset="utf-8">
<title>NORVEX Business Card</title>
<link rel="stylesheet" href="https://fonts.googleapis.com/css2?family=Open+Sans:wght@400;600;700&display=swap">
<style>
  :root {
    --stage: #222222;
    --card: #1f1f24;
    --card-deep: #17171b;
    --mint: #c3dfc0;
    --blue: #2447a0;
    --white: #ffffff;
  }
  * { margin: 0; padding: 0; box-sizing: border-box; }
  html, body { width: 1200px; height: 780px; overflow: hidden; }
  body {
    background: var(--stage);
    font-family: "Open Sans", Arial, sans-serif;
    position: relative;
  }
  .card {
    position: absolute;
    top: 235px;
    width: 540px;
    height: 310px;
    background: var(--card);
    border: 4px solid var(--mint);
    border-radius: 18px;
    overflow: hidden;
  }
  .card--back { left: 40px; }
  .card--front { left: 620px; }

  .back-pattern {
    position: absolute;
    inset: 0;
    background: linear-gradient(135deg, #1a1a1e 0%, #2a2a30 45%, #19191c 100%);
  }
  .back-brand {
    position: absolute;
    right: 70px;
    bottom: 70px;
    font-size: 18px;
    font-weight: 700;
    color: var(--mint);
    letter-spacing: 1px;
  }

  .brand {
    position: absolute;
    left: 28px;
    top: 22px;
    font-size: 60px;
    font-weight: 700;
    color: var(--mint);
    letter-spacing: 2px;
    line-height: 1;
  }
  .name-tab {
    position: absolute;
    left: 22px;
    top: 150px;
    width: 10px;
    height: 54px;
    background: var(--mint);
  }
  .person { position: absolute; left: 44px; top: 144px; }
  .person-name { font-size: 32px; font-weight: 700; line-height: 1.1; }
  .person-first { color: var(--blue); }
  .person-last { color: var(--mint); }
  .person-title { font-size: 14px; font-weight: 600; color: var(--white); }
  .rule {
    position: absolute;
    left: 245px;
    right: 24px;
    top: 197px;
    height: 2px;
    background: var(--white);
  }
  .contacts {
    position: absolute;
    left: 56px;
    top: 222px;
    list-style: none;
    color: var(--white);
    font-size: 13px;
    line-height: 20px;
  }
  .contacts li { display: flex; align-items: center; gap: 8px; }
  .contacts svg { width: 13px; height: 13px; }
  .address {
    position: absolute;
    right: 26px;
    top: 214px;
    text-align: right;
    color: var(--white);
    font-size: 12.5px;
    line-height: 18px;
  }
  .bands { position: absolute; left: 0; top: 0; width: 540px; height: 310px; }
</style>
</head>
<body>
  <section class="card card--back">
    <div class="back-pattern" role="img" aria-label="Repeating embossed brand name pattern in dark tones"></div>
    <div class="back-brand">NORVEX</div>
  </section>

  <section class="card card--front">
    <svg class="bands" viewBox="0 0 540 310" aria-hidden="true">
      <polygon points="110,310 140,286 390,286 410,278 420,310" fill="var(--blue)"/>
      <polygon points="390,310 420,262 540,262 540,310" fill="var(--mint)"/>
    </svg>
    <div class="brand">NORVEX</div>
    <div class="name-tab"></div>
    <div class="person">
      <div class="person-name"><span class="person-first">Mira</span> <span class="person-last">Lin</span></div>
      <div class="person-title">Chief Operating Officer</div>
    </div>
    <div class="rule"></div>
    <ul class="contacts">
      <li>
        <svg viewBox="0 0 14 14"><rect x="3.5" y="1" width="7" height="12" rx="1.2" fill="none" stroke="var(--white)" stroke-width="1.2"/></svg>
        +65 9000 1234
      </li>
      <li>
        <svg viewBox="0 0 14 14"><circle cx="7" cy="7" r="6" fill="var(--blue)"/><path d="M1 7h12M7 1c-3 3-3 9 0 12M7 1c3 3 3 9 0 12" fill="none" stroke="var(--white)" stroke-width="0.8"/></svg>
        www.norvex.com
      </li>
      <li>
        <svg viewBox="0 0 14 14"><rect x="1" y="3" width="12" height="8" fill="none" stroke="var(--white)" stroke-width="1.2"/><path d="M1 3l6 5 6-5" fill="none" stroke="var(--white)" stroke-width="1.2"/></svg>
        mira@norvex.com
      </li>
    </ul>
    <address class="address" style="font-style:normal">
      25 Harbour Lane, Marina<br>
      Tower #08-02, Singapore 018900
    </address>
  </section>
</body>
</html>
```